IT Services Company Needs Corporate PPT Template

This is urgent (need a fast turn around). We need a corporate PPT template deck (NOTE: Deck should be in 4:3 ratio) for our IT Services firm that is clean but slick and modern. We tend to lean more towards the flat design look. I'm attaching a zip file which includes our Corporate Branding Guide (which is in progress), color scheme, A PPT deck as inspiration (our logo is on the last slide), our font (LATO). Our newly launched website is located at: http://www.veranthix.com.

As an example of a deck we like see: http://slidemorrow.net/item/clean-multipurpose-business-presentation-template/5318206?WT.ac=category_thumb&WT.seg_1=category_thumb&WT.z_author=PixelHarbor
Although we don't want "this" deck - it gives an idea of style.

I'm also attaching a copy of our corporate deck as it is now to give you an idea of the type of content that would appear on various slides. We definitely want the following slides (at least) within the template:

Title Slide
Blank Slide
2 Column - with bullets
2 Column - no bullets
Single Column - no bullets
Single Column - with bullets
Various Charts and Tables (see example deck)
Meet the Team
Offering Slide
Customer Showcase
Timeline
Case Study
Contact US

Note: Being awarded this job will lead to a second job of creating our corporate deck.

Target Market(s)

CIO, CEO, Technology Officers, Sales People, Marketing, IT heads and staff, Customers, Prospective customers

Industry/Entity Type

Business

Requirements
Must have
• See description and attached files

```html
<!DOCTYPE html>
<html lang="en">
<head>
<meta charset="UTF-8">
<title>Project Title Here</title>
<link href="https://fonts.googleapis.com/css2?family=Open+Sans:wght@400;600;700;800&display=swap" rel="stylesheet">
<style>
  :root {
    --page-bg: #efedee;
    --header-blue: #1f6f93;
    --header-blue-dark: #0f5878;
    --header-edge: #0b3e5c;
    --heading-blue: #1b72a8;
    --body-text: #2a2a2a;
    --footer-top: #f7f7f8;
    --footer-bottom: #dcdde0;
    --footer-rule: #c9cbce;
    --muted-text: #6d6f73;
    --brand-ink: #1b1b1b;
  }
  html, body {
    margin: 0;
    padding: 0;
    overflow: hidden;
  }
  body {
    width: 1200px;
    height: 900px;
    background: #ffffff;
    font-family: "Open Sans", Arial, sans-serif;
  }
  .slide {
    position: relative;
    width: 1200px;
    height: 900px;
    background: var(--page-bg);
    overflow: hidden;
  }
  .slide-header {
    position: absolute;
    top: 0;
    left: 0;
    width: 1200px;
    height: 150px;
  }
  .slide-header svg {
    display: block;
  }
  .slide-title {
    position: absolute;
    top: 28px;
    left: 64px;
    margin: 0;
    color: #ffffff;
    font-size: 43px;
    font-weight: 600;
    letter-spacing: -0.3px;
    line-height: 1.1;
  }
  .content {
    position: absolute;
    left: 70px;
    width: 1040px;
  }
  .content--first { top: 188px; }
  .content--second { top: 505px; }
  .section-heading {
    margin: 0 0 6px;
    color: var(--heading-blue);
    font-size: 28px;
    font-weight: 400;
    line-height: 1.3;
    letter-spacing: -0.2px;
  }
  .section-body {
    margin: 0;
    color: var(--body-text);
    font-size: 19px;
    line-height: 36px;
    letter-spacing: -0.15px;
  }
  .content--second .section-body { padding-left: 4px; }
  .slide-footer {
    position: absolute;
    left: 0;
    bottom: 0;
    width: 1200px;
    height: 82px;
    background: linear-gradient(var(--footer-top), var(--footer-bottom));
    border-top: 2px solid var(--footer-rule);
  }
  .brand-name {
    position: absolute;
    left: 30px;
    top: 16px;
    margin: 0;
    color: var(--brand-ink);
    font-size: 36px;
    font-weight: 800;
    letter-spacing: 0.5px;
    line-height: 1.2;
  }
  .copyright {
    position: absolute;
    right: 22px;
    top: 32px;
    margin: 0;
    color: var(--muted-text);
    font-size: 17px;
  }
</style>
</head>
<body>
  <main class="slide">
    <header class="slide-header">
      <svg width="1200" height="150" viewBox="0 0 1200 150" role="img" aria-label="Blue header band with a soft hexagon texture">
        <defs>
          <linearGradient id="headerFill" x1="0" y1="0" x2="1" y2="1">
            <stop offset="0" stop-color="var(--header-blue-dark)"/>
            <stop offset="0.5" stop-color="var(--header-blue)"/>
            <stop offset="1" stop-color="var(--header-blue-dark)"/>
          </linearGradient>
        </defs>
        <polygon points="0,0 1200,0 1200,84 0,140" fill="url(#headerFill)"/>
        <polygon points="0,136 1200,80 1200,84 0,146" fill="var(--header-edge)"/>
      </svg>
      <h1 class="slide-title">Project Title Here</h1>
    </header>

    <section class="content content--first">
      <h2 class="section-heading">Lorem ipsum dolor sit ipsum Lorem ipsum</h2>
      <p class="section-body">Lorem ipsum dolor sit ipsum Lorem ipsum dolor sit ipsum Lorem ipsum dolor sit ipsum Lorem ipsum dolor sit ipsum lorem ipsum dolor sit ipsum Lorem ipsum dolor sit ipsum Lorem ipsum dolor sit ipsum Lorem ipsum dolor sit ipsum Lorem ipsum dolor sit ipsum lorem ipsum dolor sit ipsum Lorem ipsum dolor sit ipsum Lorem ipsum dolor sit ipsum Lorem ipsum dolor sit ipsum Lorem ipsum dolor sit ipsum lorem ipsum dolor sit ipsum Lorem ipsum dolor sit ipsum Lorem ipsum dolor sit ipsum Lorem ipsum dolor sit ipsum Lorem ipsum dolor sit ipsum lorem ipsum dolor sit ipsum</p>
    </section>

    <section class="content content--second">
      <h2 class="section-heading">Lorem ipsum dolor sit ipsum Lorem ipsum</h2>
      <p class="section-body">Dolor sit ipsum Lorem ipsum dolor sit ipsum Lorem ipsum dolor sit ipsum lorem ipsum dolor sit ipsum Lorem ipsum dolor sit ipsum Lorem ipsum dolor sit ipsum Lorem ipsum dolor sit ipsum Lorem ipsum dolor sit ipsum lorem ipsum dolor sit ipsum Lorem ipsum dolor sit ipsum Lorem ipsum dolor sit ipsum Lorem ipsum dolor sit ipsum Lorem ipsum dolor sit ipsum lorem ipsum dolor sit ipsum Lorem ipsum dolor sit ipsum Lorem ipsum dolor sit ipsum Lorem ipsum dolor sit ipsum Lorem ipsum dolor sit ipsum lorem ipsum dolor sit ipsum</p>
    </section>

    <footer class="slide-footer">
      <p class="brand-name">Veranthix</p>
      <p class="copyright">Copyright text here</p>
    </footer>
  </main>
</body>
</html>
```